Business card for marketing analytics company

Need a business card for new company. I have a logo already that I want to be built into the card and should use those colours

Company is called steered by tallies
Design must bring steered by tallies to life not be a card that could be for anyone with a logo put on it.

Like the front to be fairly clean and uncluttered bringing the logo out with a suitable design on the back of the card.

The logo represents a compass and business growth so those themes along with numbers, analytics , data are appropriate.
I'm often working with creative industries so also needs to reflect the creative side of analytics rather than be very corporate looking.

Target Market(s)

Ad agency, media agency, consumer goods clients

Industry/Entity Type

Market Research

Contact Information for Business Card

Needs to include name, title, email and phone number

Colors
f78f20
f68d4d
ec1f27

Requirements
Must have
• Must bring steered by tallies to life not be a card that could be for anyone with a logo put on it.
• Logo, Correct colours
• Like a design on the back that relates to company name
• Designs for both sides
Should not have
• Please do not just submit logo and a coloured card.
• It needs to have a design element to it
• No black background
• No clear cards - needs front & back

```html
<!DOCTYPE html>
<html lang="en">
<head>
<meta charset="utf-8">
<title>Steered by Tallies — Business Card</title>
<link rel="stylesheet" href="https://fonts.googleapis.com/css2?family=Open+Sans:wght@400;600;700&display=swap">
<style>
  :root {
    --backdrop: #26272a;
    --card: #464950;
    --card-edge: #55585f;
    --silver: #dedede;
    --white: #f4f4f4;
    --muted: #d6d6d6;
    --orange: #f78f20;
    --orange-soft: #f68d4d;
    --red: #ec1f27;
    --divider: #9a9a9a;
  }
  * { margin: 0; padding: 0; box-sizing: border-box; }
  html, body { width: 1200px; height: 1000px; overflow: hidden; }
  body {
    background: var(--backdrop);
    font-family: "Open Sans", Arial, sans-serif;
    position: relative;
  }
  .card {
    position: absolute;
    left: 220px;
    width: 760px;
    background: var(--card);
    border: 1px solid var(--card-edge);
    box-shadow: 0 18px 40px rgba(0,0,0,0.45);
    overflow: hidden;
  }
  .card--front { top: 50px; height: 410px; }
  .card--back { top: 520px; height: 430px; }

  .brand {
    position: absolute;
    display: flex;
    align-items: center;
    gap: 22px;
  }
  .brand__dot { border-radius: 50%; flex: none; }
  .brand__name { font-weight: 600; line-height: 1.05; }

  .card--front .brand { left: 230px; top: 145px; }
  .card--front .brand__dot { width: 100px; height: 100px; border: 4px solid var(--silver); }
  .card--front .brand__name { font-size: 34px; color: var(--silver); }

  .card--back .brand { left: 70px; top: 130px; width: 350px; }
  .card--back .brand__dot { width: 130px; height: 130px; border: 6px solid var(--orange); }
  .card--back .brand__name { font-size: 24px; color: var(--orange); }

  .bearing-scale {
    position: absolute;
    left: 0; bottom: 34px;
    width: 760px; height: 40px;
  }
  .growth-bars {
    position: absolute;
    left: 0; bottom: 0;
    width: 760px; height: 70px;
  }

  .divider {
    position: absolute;
    left: 440px; top: 95px;
    width: 3px; height: 200px;
    background: var(--divider);
  }
  .contact { position: absolute; left: 468px; top: 90px; }
  .contact__name { font-size: 29px; font-weight: 700; color: var(--orange); line-height: 1.1; }
  .contact__title { font-size: 19px; font-weight: 600; color: var(--white); margin-bottom: 12px; }
  .contact__address { font-size: 18px; color: var(--muted); line-height: 1.3; margin-bottom: 8px; }
  .contact__list { list-style: none; }
  .contact__item {
    display: flex; align-items: center; gap: 14px;
    font-size: 20px; color: var(--white); line-height: 1.5;
  }
  .contact__item svg { width: 16px; height: 16px; flex: none; }
  .contact__accent { color: var(--orange); }
</style>
</head>
<body>
  <section class="card card--front" aria-label="Card front">
    <div class="brand">
      <span class="brand__dot"></span>
      <span class="brand__name">Steered by<br>Tallies</span>
    </div>
    <svg class="bearing-scale" viewBox="0 0 760 40" aria-hidden="true">
      <line x1="60" y1="30" x2="700" y2="30" stroke="#8d9097" stroke-width="1"/>
      <g stroke="#8d9097" stroke-width="1">
        <line x1="60" y1="30" x2="60" y2="14"/><line x1="92" y1="30" x2="92" y2="24"/><line x1="124" y1="30" x2="124" y2="24"/><line x1="156" y1="30" x2="156" y2="24"/>
        <line x1="188" y1="30" x2="188" y2="18"/><line x1="220" y1="30" x2="220" y2="24"/><line x1="252" y1="30" x2="252" y2="24"/><line x1="284" y1="30" x2="284" y2="24"/>
        <line x1="316" y1="30" x2="316" y2="14"/><line x1="348" y1="30" x2="348" y2="24"/><line x1="412" y1="30" x2="412" y2="24"/><line x1="444" y1="30" x2="444" y2="14"/>
        <line x1="476" y1="30" x2="476" y2="24"/><line x1="508" y1="30" x2="508" y2="24"/><line x1="540" y1="30" x2="540" y2="24"/><line x1="572" y1="30" x2="572" y2="18"/>
        <line x1="604" y1="30" x2="604" y2="24"/><line x1="636" y1="30" x2="636" y2="24"/><line x1="668" y1="30" x2="668" y2="24"/><line x1="700" y1="30" x2="700" y2="14"/>
      </g>
      <path d="M380 4 L386 22 L380 18 L374 22 Z" fill="#f78f20"/>
    </svg>
  </section>

  <section class="card card--back" aria-label="Card back">
    <div class="brand">
      <span class="brand__dot"></span>
      <span class="brand__name">Steered by<br>Tallies</span>
    </div>
    <div class="divider"></div>
    <div class="contact">
      <p class="contact__name">Dara Quinlan</p>
      <p class="contact__title">Ceo/Founer</p>
      <p class="contact__address">14 Ledger Lane,<br>Port Aldin, 5821</p>
      <ul class="contact__list">
        <li class="contact__item">
          <svg viewBox="0 0 16 16" aria-hidden="true"><path fill="#f78f20" d="M3 1l3 3-1.5 2c1 2 3 4 5 5L11.5 9.5l3 3-2 2.5C7 14 2 9 1 3z"/></svg>
          +000 555 204 871
        </li>
        <li class="contact__item">
          <svg viewBox="0 0 16 16" aria-hidden="true"><rect x="1" y="3" width="14" height="10" fill="#f78f20"/><path d="M1 3l7 6 7-6" fill="none" stroke="#464950" stroke-width="1.5"/></svg>
          dara@tallymail.com
        </li>
        <li class="contact__item">
          <svg viewBox="0 0 16 16" aria-hidden="true"><circle cx="9" cy="7" r="5" fill="none" stroke="#f78f20" stroke-width="2"/><path d="M5.5 10.5L1.5 14.5" stroke="#f78f20" stroke-width="2.5"/></svg>
          <span>www.<span class="contact__accent">steeredtallies</span>.com</span>
        </li>
      </ul>
    </div>
    <svg class="growth-bars" viewBox="0 0 760 70" aria-hidden="true">
      <g opacity="0.85">
        <rect x="0" y="62" width="52" height="8" fill="#ec1f27"/>
        <rect x="56" y="58" width="52" height="12" fill="#ec1f27"/>
        <rect x="112" y="60" width="52" height="10" fill="#ec1f27"/>
        <rect x="168" y="54" width="52" height="16" fill="#ec1f27"/>
        <rect x="224" y="50" width="52" height="20" fill="#f68d4d"/>
        <rect x="280" y="52" width="52" height="18" fill="#f68d4d"/>
        <rect x="336" y="44" width="52" height="26" fill="#f68d4d"/>
        <rect x="392" y="40" width="52" height="30" fill="#f68d4d"/>
        <rect x="448" y="34" width="52" height="36" fill="#f78f20"/>
        <rect x="504" y="36" width="52" height="34" fill="#f78f20"/>
        <rect x="560" y="26" width="52" height="44" fill="#f78f20"/>
        <rect x="616" y="20" width="52" height="50" fill="#f78f20"/>
        <rect x="672" y="12" width="52" height="58" fill="#f78f20"/>
        <rect x="728" y="6" width="32" height="64" fill="#f78f20"/>
      </g>
    </svg>
  </section>
</body>
</html>
```